Personal letterhead and stationary

I am looking for someone to design letterhead and stationary set for my personal use. I want something simple and timeless with a little bit of color. I like photography, computers and writing.

```html
<!DOCTYPE html>
<html lang="en">
<head>
<meta charset="utf-8">
<title>Marcus James Hale – Letterhead</title>
<link rel="stylesheet" href="https://fonts.googleapis.com/css2?family=Josefin+Slab:wght@400;600;700&display=swap">
<style>
  :root {
    --backdrop: #5b5b5b;
    --paper: #ffffff;
    --ink: #111111;
    --accent: #1f7a8c;
    --rule-soft: #9cc7cf;
  }
  * { margin: 0; padding: 0; box-sizing: border-box; }
  html, body {
    width: 854px;
    height: 1200px;
    overflow: hidden;
    background: var(--backdrop);
  }
  .sheet {
    position: absolute;
    left: 11px;
    top: 11px;
    width: 832px;
    height: 1180px;
    background: var(--paper);
    font-family: "Josefin Slab", Georgia, serif;
    color: var(--ink);
  }
  .header-rule {
    position: absolute;
    left: 80px;
    width: 688px;
    height: 1px;
    background: var(--ink);
  }
  .header-rule--upper { top: 142px; }
  .header-rule--lower { top: 148px; background: var(--accent); }
  .owner-name {
    position: absolute;
    left: 86px;
    top: 111px;
    font-size: 21px;
    font-weight: 700;
    letter-spacing: 0;
    word-spacing: 4px;
    line-height: 1;
  }
  .owner-email {
    position: absolute;
    left: 85px;
    top: 154px;
    font-size: 13px;
    line-height: 1;
  }
  .owner-phone {
    position: absolute;
    right: 82px;
    top: 114px;
    font-size: 18px;
    font-weight: 600;
    line-height: 1;
    display: flex;
    align-items: center;
    gap: 6px;
  }
  .owner-phone svg { width: 14px; height: 18px; }
  .owner-address {
    position: absolute;
    right: 64px;
    top: 154px;
    font-size: 13px;
    line-height: 1;
  }
  .brand-mark {
    position: absolute;
    left: 356px;
    top: 86px;
    width: 122px;
    height: 122px;
    border-radius: 50%;
    border: 3px solid var(--accent);
    background: var(--paper);
    display: flex;
    align-items: center;
    justify-content: center;
    text-align: center;
    font-size: 17px;
    font-weight: 700;
    line-height: 1.15;
    letter-spacing: 1px;
    color: var(--accent);
  }
  .footer-rule {
    position: absolute;
    left: 62px;
    top: 1139px;
    width: 714px;
    height: 1px;
    background: var(--rule-soft);
  }
  .footer-quote {
    position: absolute;
    left: 0;
    top: 1147px;
    width: 100%;
    text-align: center;
    font-size: 11px;
    font-weight: 600;
    letter-spacing: 1.3px;
    line-height: 16px;
  }
</style>
</head>
<body>
  <main class="sheet">
    <div class="header-rule header-rule--upper"></div>
    <div class="header-rule header-rule--lower"></div>

    <h1 class="owner-name">MARCUS JAMES HALE</h1>
    <p class="owner-email">marcus@example.com.au</p>

    <div class="brand-mark">MARCUS<br>HALE</div>

    <p class="owner-phone">
      <svg viewBox="0 0 15 19" aria-hidden="true">
        <path d="M4 1 L7 5 L5 7.5 C5.5 10 7 12.5 9 14 L11.5 12.5 L14 16 L11 18.5 C6 17 2 11 2.5 4 Z" fill="#1f7a8c"/>
      </svg>
      040000123456
    </p>
    <p class="owner-address">14 elm st bendale vic 4500</p>

    <div class="footer-rule"></div>
    <p class="footer-quote">Be the change you want to see in the World<br>-Arthur Penrose</p>
  </main>
</body>
</html>
```